Real estate agent website

I am a new real estate agent and in of a simple but powerful website that is linked to the local Multiple listing services (MLS). It should have a lending page that is connected to my customer relationship management (CRM) software. It must have an ability for potential customers to search for properties and be able to communicate with me easily.
Updates

Updates: The website themes must includes MLS-IDX integration with a grid layout and property slider so i can showcase featured properties. I also would like to have future where potential client can search and have alerts depending on a search criteria.

Industry/Entity Type

Real Estate

Coding

Coded - Design and coding required

Number of Pages Required

3 page

Requirements
Must have
• Home page, Resources page, About Me with contact me window page

```html
<!DOCTYPE html>
<html lang="en">
<head>
<meta charset="utf-8">
<title>Marina Holt Real Estate Agent</title>
<link href="https://fonts.googleapis.com/css2?family=Bebas+Neue&family=Lato:ital,wght@0,400;0,700;1,400&display=swap" rel="stylesheet">
<style>
:root{
  --ink:#4a4c57;
  --gold:#c98a3a;
  --white:#ffffff;
  --text:#2b2b2b;
  --muted:#9a9a9a;
  --line:#e6e6e6;
}
*{box-sizing:border-box;margin:0;padding:0}
html,body{width:1200px;height:3666px;overflow:hidden}
body{position:relative;background:var(--white);font-family:"Lato",sans-serif;color:var(--text)}
.abs{position:absolute}
.display{font-family:"Bebas Neue",sans-serif;font-weight:400;letter-spacing:.3px}

/* hero */
.hero-panel{left:0;top:0;width:492px;height:666px;background:var(--ink)}
.hero-photo{left:492px;top:0;width:708px;height:666px;background:linear-gradient(180deg,#9cc3e6 0%,#c9dbe8 35%,#8c9a86 58%,#b9b9b2 72%,#5f8a3d 90%,#4c7a2e 100%)}
.topbar{left:492px;top:0;width:519px;height:43px;background:var(--gold);border-radius:0 0 22px 0;color:var(--white);font-size:14px;display:flex;align-items:center;padding-left:18px;gap:26px}
.topbar span{display:flex;align-items:center;gap:9px}
.login{left:1028px;top:12px;color:var(--white);font-size:15px;font-weight:700;display:flex;gap:7px;align-items:center}
.nav{left:0;top:76px;width:1200px;color:var(--white);font-size:15px}
.nav a{color:inherit;text-decoration:none;position:absolute;white-space:nowrap}
.brand{font-family:"Lato",sans-serif;font-weight:400;color:var(--gold);letter-spacing:2px;white-space:nowrap}
.brand-top{left:112px;top:26px;font-size:26px}
.welcome{left:112px;top:224px;color:var(--gold);font-size:25px}
.hero-title{left:110px;top:262px;color:var(--white);font-size:88px;line-height:107px}
.btn{display:flex;align-items:center;justify-content:center;border-radius:27px;font-family:"Bebas Neue",sans-serif;font-size:19px}
.btn-gold{left:112px;top:491px;width:154px;height:53px;background:var(--gold);color:var(--white)}

/* search */
.search{left:112px;top:632px;width:976px;height:248px;border-radius:10px;background:linear-gradient(180deg,rgba(201,138,58,.93),rgba(210,150,68,.95));text-align:center}
.search h2{color:var(--white);font-size:38px;margin-top:45px}
.search-input{position:absolute;left:106px;top:120px;width:763px;height:65px;background:var(--white);border-radius:33px;display:flex;align-items:center;padding-left:34px;gap:14px;font-size:15px;color:#777}
.search-go{position:absolute;right:10px;top:10px;width:46px;height:46px;border-radius:50%;background:var(--ink);display:flex;align-items:center;justify-content:center}

.section-title{width:1200px;left:0;text-align:center;color:#1d1d1d;font-size:38px}

/* cards */
.card{width:313px;height:416px;background:var(--white);border-radius:18px;box-shadow:0 3px 14px rgba(0,0,0,.12);overflow:hidden}
.card-photo{height:225px;position:relative}
.tag{position:absolute;right:20px;top:20px;background:var(--gold);color:var(--white);font-size:13px;font-weight:700;padding:6px 10px;border-radius:14px}
.card-body{padding:20px 26px 0 21px}
.price{font-size:21px;color:#1d1d1d}
.card-title{font-size:18px;color:#1d1d1d;margin-top:12px}
.loc{display:flex;align-items:center;gap:8px;color:var(--muted);font-size:14px;margin-top:14px}
.specs{border-top:1px solid var(--line);margin-top:14px;padding-top:14px;display:flex;gap:24px;font-size:14px;color:#333;padding-left:8px}
.specs span{display:flex;align-items:center;gap:7px}

/* about */
.about{left:0;top:2028px;width:1200px;height:563px;background:linear-gradient(90deg,var(--gold) 0%,var(--gold) 40%,#c99858 58%,#8a8a70 80%,#6d8a4a 100%)}
.about h2{position:absolute;left:110px;top:72px;color:var(--white);font-size:38px;line-height:47px}
.about p{position:absolute;left:114px;top:178px;width:392px;color:var(--white);font-size:15px;line-height:25.8px}
.btn-white{left:113px;top:434px;width:154px;height:53px;background:var(--white);color:var(--gold)}
.portrait{left:628px;top:50px;width:464px;height:464px;border-radius:50%;border:8px solid var(--white);background:radial-gradient(circle at 50% 45%,#e9c6a8 0%,#c8906a 40%,#a5a9ad 72%,#7c8792 100%)}

/* testimonials */
.quote{left:574px;top:2664px;width:62px;height:62px;border-radius:50%;background:var(--gold);color:var(--white);font-family:Georgia,serif;font-size:56px;font-weight:700;text-align:center;line-height:78px}
.test-intro{left:280px;top:2794px;width:640px;text-align:center;font-size:13.5px;line-height:26px;color:#555}
.tcard{top:2887px;width:409px;height:195px;background:var(--white);box-shadow:0 2px 14px rgba(0,0,0,.07);padding:24px 24px;font-style:italic;font-size:13.5px;line-height:26px;color:#555}
.tcard.faded{opacity:.45}
.who{display:flex;align-items:center;gap:14px;margin-top:12px;font-style:normal}
.avatar{width:50px;height:50px;border-radius:50%;background:linear-gradient(180deg,#d9d4cf,#8d8f96)}
.who b{display:block;font-family:"Bebas Neue",sans-serif;font-weight:400;color:var(--gold);font-size:18px;line-height:20px}
.who em{font-style:normal;font-size:15px;color:#888}
.dots{left:584px;top:3144px;display:flex;gap:6px}
.dots i{width:10px;height:10px;border-radius:50%;background:#bbb}
.dots i:first-child{background:var(--gold)}

/* footer */
.footer{left:0;top:3256px;width:1200px;height:410px;background:var(--ink);color:var(--white)}
.brand-foot{left:111px;top:100px;font-size:31px}
.f-about{position:absolute;left:111px;top:164px;width:295px;font-size:13.5px;line-height:26px}
.f-col{position:absolute;top:100px}
.f-col h3{font-family:"Bebas Neue",sans-serif;font-weight:400;font-size:24px;margin-bottom:20px}
.f-col li{list-style:none;font-size:15px;line-height:30px;display:flex;gap:10px;align-items:flex-start}
.social{display:flex;gap:8px}
.social i{width:32px;height:32px;border-radius:50%;background:var(--white)}
.social i:first-child{background:var(--gold)}
.copy{position:absolute;left:0;width:1200px;top:350px;text-align:center;font-size:15px}
</style>
</head>
<body>

<!-- hero -->
<div class="abs hero-panel"></div>
<div class="abs hero-photo" role="img" aria-label="Photo of a two-storey suburban family house with a driveway and green lawn"></div>
<div class="abs topbar">
  <span><svg width="12" height="15" viewBox="0 0 12 16"><path d="M6 0a6 6 0 0 0-6 6c0 4.5 6 10 6 10s6-5.5 6-10a6 6 0 0 0-6-6zm0 8.5A2.5 2.5 0 1 1 6 3.5a2.5 2.5 0 0 1 0 5z" fill="#fff"/></svg>412 Cedar Ave Ste 110, Lakeview, Mn, 55012</span>
  <span><svg width="14" height="14" viewBox="0 0 16 16"><path d="M3.6 1 6 4.2 4.5 6a9 9 0 0 0 5.5 5.5L11.8 10 15 12.4 13.4 15C6.5 14.5 1.5 9.5 1 2.6z" fill="#fff"/></svg>(555) 204-3188</span>
</div>
<div class="abs login"><svg width="13" height="14" viewBox="0 0 14 14"><circle cx="7" cy="4" r="3.5" fill="#c98a3a"/><path d="M0 14a7 6 0 0 1 14 0z" fill="#c98a3a"/></svg>Login</div>
<nav class="abs nav">
  <a style="left:612px">Home</a><a style="left:695px">About Us</a><a style="left:800px">Lending</a><a style="left:896px">Buy</a><a style="left:962px">Sell</a><a style="left:1018px">Contact Us</a>
</nav>
<div class="abs brand brand-top">MARINA HOLT</div>
<div class="abs welcome display">WELCOME TO</div>
<h1 class="abs hero-title display">MARINA HOLT<br>REAL ESTATE AGENT</h1>
<div class="abs btn btn-gold">LEARN MORE</div>

<!-- search -->
<section class="abs search">
  <h2 class="display">BEGIN YOUR SEARCH BELOW</h2>
  <div class="search-input">
    <svg width="11" height="14" viewBox="0 0 12 16"><path d="M6 0a6 6 0 0 0-6 6c0 4.5 6 10 6 10s6-5.5 6-10a6 6 0 0 0-6-6zm0 8.5A2.5 2.5 0 1 1 6 3.5a2.5 2.5 0 0 1 0 5z" fill="#c98a3a"/></svg>
    Start your search by City, Neighborhood or Zipcode
    <div class="search-go"><svg width="14" height="14" viewBox="0 0 14 14"><circle cx="6" cy="6" r="4.2" stroke="#fff" stroke-width="2" fill="none"/><path d="M9 9l4 4" stroke="#fff" stroke-width="2"/></svg></div>
  </div>
</section>

<h2 class="abs section-title display" style="top:982px">FEATURED LISTINGS</h2>

<svg width="0" height="0" style="position:absolute">
  <defs>
    <symbol id="pin" viewBox="0 0 12 16"><path d="M6 0a6 6 0 0 0-6 6c0 4.5 6 10 6 10s6-5.5 6-10a6 6 0 0 0-6-6zm0 8.5A2.5 2.5 0 1 1 6 3.5a2.5 2.5 0 0 1 0 5z" fill="#c98a3a"/></symbol>
    <symbol id="area" viewBox="0 0 16 12"><path d="M2 4h10l-2-2M14 8H4l2 2" stroke="#999" stroke-width="1.4" fill="none"/></symbol>
    <symbol id="car" viewBox="0 0 16 12"><path d="M2 6l2-4h8l2 4v4H2z" fill="#aaa"/></symbol>
    <symbol id="bath" viewBox="0 0 16 14"><path d="M2 1h3v6h9v3a3 3 0 0 1-3 3H5a3 3 0 0 1-3-3z" fill="#aaa"/></symbol>
  </defs>
</svg>

<!-- listing row 1 -->
<article class="abs card" style="left:114px;top:1085px">
  <div class="card-photo" role="img" aria-label="Photo of a bright bathroom with dark vanity and mirrors" style="background:linear-gradient(180deg,#f2f2f2,#d9d9d9 55%,#3a3a3a 56%,#2e2e2e 85%,#e2e2e2 86%)"><span class="tag">Homes Available</span></div>
  <div class="card-body"><div class="price display">$500,000+</div><div class="card-title display">LOREM IPSUM DOLOR SIT AMET</div>
  <div class="loc"><svg width="11" height="15"><use href="#pin"/></svg>Lorem ipsum dolor sit amet</div>
  <div class="specs"><span><svg width="16" height="12"><use href="#area"/></svg>500 Sqft</span><span><svg width="16" height="12"><use href="#car"/></svg>3</span><span><svg width="16" height="14"><use href="#bath"/></svg>4</span></div></div>
</article>
<article class="abs card" style="left:447px;top:1085px">
  <div class="card-photo" role="img" aria-label="Photo of an empty room with wood floor and a window" style="background:linear-gradient(180deg,#f4f4f4 0%,#e9e9e9 60%,#8a6a4c 61%,#6e5038 100%)"></div>
  <div class="card-body"><div class="price display">$369,900+</div><div class="card-title display">LOREM IPSUM DOLOR SIT AMET</div>
  <div class="loc"><svg width="11" height="15"><use href="#pin"/></svg>Lorem ipsum dolor sit amet</div>
  <div class="specs"><span><svg width="16" height="12"><use href="#area"/></svg>500 Sqft</span><span><svg width="16" height="12"><use href="#car"/></svg>3</span><span><svg width="16" height="14"><use href="#bath"/></svg>4</span></div></div>
</article>
<article class="abs card" style="left:779px;top:1085px">
  <div class="card-photo" role="img" aria-label="Photo of a large two-storey house at dusk with lawn" style="background:linear-gradient(180deg,#6f9ad6 0%,#a9bedc 40%,#8d8c8a 62%,#4e8a34 80%,#3f7a2a 100%)"></div>
  <div class="card-body"><div class="price display">$369,900+</div><div class="card-title display">LOREM IPSUM DOLOR SIT AMET</div>
  <div class="loc"><svg width="11" height="15"><use href="#pin"/></svg>Lorem ipsum dolor sit amet</div>
  <div class="specs"><span><svg width="16" height="12"><use href="#area"/></svg>500 Sqft</span><span><svg width="16" height="12"><use href="#car"/></svg>3</span><span><svg width="16" height="14"><use href="#bath"/></svg>2</span></div></div>
</article>

<!-- listing row 2 -->
<article class="abs card" style="left:114px;top:1525px">
  <div class="card-photo" role="img" aria-label="Photo of a dark modern farmhouse lit at night" style="background:linear-gradient(180deg,#2f4e86 0%,#3d5370 45%,#3b3b40 70%,#2f3b2a 100%)"></div>
  <div class="card-body"><div class="price display">$369,900+</div><div class="card-title display">LOREM IPSUM DOLOR SIT AMET</div>
  <div class="loc"><svg width="11" height="15"><use href="#pin"/></svg>Lorem ipsum dolor sit amet</div>
  <div class="specs"><span><svg width="16" height="12"><use href="#area"/></svg>2508&nbsp; Sqft</span><span><svg width="16" height="12"><use href="#car"/></svg>2</span><span><svg width="16" height="14"><use href="#bath"/></svg>2</span></div></div>
</article>
<article class="abs card" style="left:447px;top:1525px">
  <div class="card-photo" role="img" aria-label="Photo of a white craftsman house with porch and trees" style="background:linear-gradient(180deg,#6a9be0 0%,#a3c1e3 30%,#d4d4d2 55%,#9a9a96 70%,#5a8e3a 88%,#4b7d2e 100%)"></div>
  <div class="card-body"><div class="price display">$369,900+</div><div class="card-title display">LOREM IPSUM DOLOR SIT AMET</div>
  <div class="loc"><svg width="11" height="15"><use href="#pin"/></svg>Lorem ipsum dolor sit amet</div>
  <div class="specs"><span><svg width="16" height="12"><use href="#area"/></svg>2508&nbsp; Sqft</span><span><svg width="16" height="12"><use href="#car"/></svg>2</span><span><svg width="16" height="14"><use href="#bath"/></svg>2</span></div></div>
</article>
<article class="abs card" style="left:779px;top:1525px">
  <div class="card-photo" role="img" aria-label="Photo of a modern white house with wood accents and driveway" style="background:linear-gradient(180deg,#5f95d8 0%,#a7c4e6 35%,#eeeeec 55%,#8c7152 70%,#9b9b9b 82%,#4f8a33 100%)"></div>
  <div class="card-body"><div class="price display">$369,900+</div><div class="card-title display">LOREM IPSUM DOLOR SIT AMET</div>
  <div class="loc"><svg width="11" height="15"><use href="#pin"/></svg>Lorem ipsum dolor sit amet</div>
  <div class="specs"><span><svg width="16" height="12"><use href="#area"/></svg>2508&nbsp; Sqft</span><span><svg width="16" height="12"><use href="#car"/></svg>2</span><span><svg width="16" height="14"><use href="#bath"/></svg>2</span></div></div>
</article>

<!-- about -->
<section class="abs about" role="img" aria-label="Background photo of a suburban home under a warm gold tint">
  <h2 class="display">ABOUT ME<br>MARINA HOLT&nbsp; REAL ESTATE AGENT</h2>
  <p>Lorem ipsum dolor sit amet, consectetur adipiscing elit, sed do eiusmod tempor incididunt ut labore et dolore magna aliqua. Quis ipsum suspendisse ultrices gravida. Risus commodo viverra maecenas accumsan lacus vel facilisis. Lorem ipsum dolor sit amet, consectetur adipiscing elit, sed do eiusmod tempor incididunt ut labore et dolore magna aliqua. Quis ipsum suspendisse ultrices gravida. Risus commodo viverra maecenas accumsan lacus vel facilisis.</p>
  <div class="abs btn btn-white">LEARN MORE</div>
  <div class="abs portrait" role="img" aria-label="Portrait photo of the agent"></div>
</section>

<!-- testimonials -->
<div class="abs quote">&ldquo;</div>
<h2 class="abs section-title display" style="top:2738px">TESTIMONIALS</h2>
<p class="abs test-intro">Lorem ipsum dolor sit amet, consectetur adipiscing elit, sed do eiusmod tempor incididunt ut labore et dolore magna aliqua. Quis ipsum suspendisse ultrices gravida.</p>

<div class="abs tcard faded" style="left:-248px">Lorem ipsum dolor sit amet, consectetur adipiscing elit, sed do eiusmod tempor incididunt ut labore et dolore magna aliqua. Quis ipsum suspendisse ultrices gravida.</div>
<div class="abs tcard" style="left:182px">Lorem ipsum dolor sit amet, consectetur adipiscing elit, sed do eiusmod tempor incididunt ut labore et dolore magna aliqua. Quis ipsum suspendisse ultrices gravida.
  <div class="who"><div class="avatar" role="img" aria-label="Client photo"></div><div><b>JORDAN ELLIS</b><em>Lorem Ipsum</em></div></div></div>
<div class="abs tcard" style="left:611px">Lorem ipsum dolor sit amet, consectetur adipiscing elit, sed do eiusmod tempor incididunt ut labore et dolore magna aliqua. Quis ipsum suspendisse ultrices gravida.
  <div class="who"><div class="avatar" role="img" aria-label="Client photo"></div><div><b>TALIA BROOKS</b><em>Lorem Ipsum</em></div></div></div>
<div class="abs tcard faded" style="left:1041px">Lorem ipsum dolor sit amet, consectetur adipiscing elit, sed do eiusmod tempor incididunt ut labore et dolore magna aliqua. Quis ipsum suspendisse ultrices gravida.
  <div class="who"><div class="avatar" role="img" aria-label="Client photo"></div><div><b>OWEN</b><em>Lorem Ipsum</em></div></div></div>
<div class="abs dots"><i></i><i></i><i></i></div>

<!-- footer -->
<footer class="abs footer">
  <div class="abs brand brand-foot">MARINA HOLT</div>
  <p class="f-about">Lorem ipsum dolor sit amet, consectetur adipiscing elit, sed do eiusmod tempor incididunt ut labore et dolore magna aliqua. Quis ipsum suspendisse ultrices gravida.</p>
  <div class="f-col" style="left:453px">
    <h3>CONTACT US</h3>
    <ul>
      <li><svg width="11" height="15" style="margin-top:7px"><use href="#pin"/></svg><span>412 CEDAR AVE STE 110,<br>LAKEVIEW, MN, 55012</span></li>
      <li style="margin-top:6px"><svg width="13" height="13" viewBox="0 0 16 16" style="margin-top:8px"><path d="M3.6 1 6 4.2 4.5 6a9 9 0 0 0 5.5 5.5L11.8 10 15 12.4 13.4 15C6.5 14.5 1.5 9.5 1 2.6z" fill="#fff"/></svg>(555) 204-3188</li>
      <li style="margin-top:6px"><svg width="14" height="11" viewBox="0 0 14 11" style="margin-top:10px"><rect width="14" height="11" rx="1" fill="#fff"/><path d="M0 1l7 5 7-5" stroke="#4a4c57" stroke-width="1.4" fill="none"/></svg>mholt.realty@example.com</li>
    </ul>
  </div>
  <div class="f-col" style="left:729px">
    <h3>SUPPORT</h3>
    <ul><li>Terms &amp; Conditions</li><li>Contact us</li><li>Privacy Policy</li><li>About Us</li></ul>
  </div>
  <div class="f-col" style="left:927px">
    <h3>FOLLOW US</h3>
    <div class="social" aria-label="Social links"><i></i><i></i><i></i><i></i></div>
  </div>
  <p class="copy">©Copyrights 2023&nbsp; Marina Holt Real Estate Agent&nbsp; |&nbsp;&nbsp;&nbsp; All Rights Reserved</p>
</footer>

</body>
</html>
```